Crestline Plaque & Medal Unique Business Card Design

Recently selected a new logo design and waiting to recieve print files. I've attached image for your review. We are a trophies and awards company that provides engraving on trophies, plaques, name plates, name tags, desk sets, medals, acrylics, and signage.

We are located in Monroe, Louisiana and provide this service with computerized & laser engraving equipment.

Target Market(s)

Corporate, Sport, Church, and Special Events

Industry/Entity Type

Business

Contact Information for Business Card

I'd like to see the following list on the card: Trophies, Plaques, Name Plates, Name Tags, Desk Sets, Medals, Certificates... this is accomplished with Computerized & Laser Engraving

Colors
0555a3
ec1f27
ffffff

Requirements
Must have
• I like either single or double sided. If a design can be created with a frosted card stock I'd consider single. Must be Red, White, and Blue. Dwight Palmer - Owner, 412 W 8th Ave, Monroe, La 71208 office 318-555-0148 fax 318-555-0163 email: info@crestlineplaquemedal.example, and website: www.crestlineplaquemedal.example

```html
<!DOCTYPE html>
<html lang="en">
<head>
<meta charset="utf-8">
<title>Crestline Plaque &amp; Medal – Business Card</title>
<link rel="stylesheet" href="https://fonts.googleapis.com/css2?family=Exo+2:wght@500;600;700&display=swap">
<style>
  :root {
    --brand-blue: #0555a3;
    --brand-blue-deep: #0a3f7e;
    --brand-red: #ec1f27;
    --brand-red-deep: #b3121a;
    --brand-navy: #14285a;
    --frost: #eef1f4;
    --frost-edge: #c9ced4;
    --stage: #d9d4cc;
    --text-light: #ffffff;
    --text-warm: #efe2c8;
  }
  * { box-sizing: border-box; margin: 0; padding: 0; }
  html, body {
    width: 1200px; height: 970px; overflow: hidden;
    background: var(--stage);
    font-family: "Exo 2", sans-serif;
  }
  .canvas {
    width: 1200px; height: 970px;
    display: flex; align-items: center; justify-content: center;
  }
  .card {
    position: relative;
    width: 1000px; height: 556px;
    background: linear-gradient(180deg, #f6f8fa 0%, var(--frost) 100%);
    border: 1px solid var(--frost-edge);
    box-shadow: 0 10px 30px rgba(0,0,0,0.18);
    overflow: hidden;
  }
  .brand {
    position: absolute; top: 118px; left: 0; right: 0;
    display: flex; align-items: center; justify-content: center; gap: 18px;
  }
  .brand__rule {
    width: 70px; height: 3px; background: var(--brand-blue);
  }
  .brand__dot {
    width: 26px; height: 26px; border-radius: 50%;
    background: var(--brand-blue);
  }
  .brand__name {
    font-weight: 700; font-size: 56px; line-height: 1;
    color: var(--brand-blue);
    letter-spacing: 0.5px;
  }
  .title-band {
    position: absolute; top: 252px; left: 0; width: 100%; height: 61px;
    background: linear-gradient(180deg, var(--brand-red) 0%, var(--brand-red-deep) 100%);
    display: flex; align-items: center; justify-content: center; gap: 12px;
  }
  .title-band__name {
    font-weight: 700; font-size: 35px; color: var(--text-light);
  }
  .title-band__divider {
    font-size: 26px; color: var(--text-warm); font-weight: 500;
  }
  .title-band__role {
    font-weight: 500; font-size: 27px; color: var(--text-warm);
  }
  .info-band {
    position: absolute; top: 313px; left: 0; width: 100%; height: 179px;
    background: linear-gradient(180deg, var(--brand-blue) 0%, var(--brand-blue-deep) 100%);
    text-align: center; color: var(--text-light);
    padding-top: 22px;
  }
  .info-band__contact {
    font-weight: 600; font-size: 27px; line-height: 30px;
  }
  .info-band__services {
    margin-top: 22px;
    font-weight: 600; font-size: 25px; line-height: 31px;
    color: var(--text-warm);
  }
  .address {
    position: absolute; top: 492px; left: 0; width: 100%; height: 64px;
    display: flex; align-items: center; justify-content: center;
    font-weight: 600; font-size: 29px; color: var(--brand-navy);
  }
</style>
</head>
<body>
<main class="canvas">
  <article class="card">
    <header class="brand">
      <span class="brand__rule"></span>
      <span class="brand__dot"></span>
      <h1 class="brand__name">Crestline Plaque &amp; Medal</h1>
      <span class="brand__rule"></span>
    </header>

    <section class="title-band">
      <span class="title-band__name">Employee Name</span>
      <span class="title-band__divider">|</span>
      <span class="title-band__role">Managing Director</span>
    </section>

    <section class="info-band">
      <p class="info-band__contact">0012 3456 789</p>
      <p class="info-band__contact">info@youremail.com</p>
      <p class="info-band__services">engraving on trophies, plaques, name plates, name tags, desk sets<br>medals, acrylics, and signage</p>
    </section>

    <footer class="address">Your Adress Inc&nbsp; 2nd Lane, NJ 00000</footer>
  </article>
</main>
</body>
</html>
```